Modern and Simple Supplement Label Design

We are looking for a Professional Graphic Designer who can design eye-catching and unique supplement label. We are supplement company who are sourcing different supplement products. I would like the design to be simple and with few colorsThe final design should communicate strength and growthI attached some samples for inspiration

Target Market(s)

Supplement Market - Collagen Supplements

Industry/Entity Type

Supplement

Font styles to use
Serif
Sans Serif

Colors

Designer to choose colors to be used in the design.

Requirements
Must have
• Front (Please search on Brindleport Collagen to get inspiration how to put together the front text)
• Logo: Vellow Naturals
• Product Name: Omni Dermal Capsules
• Hydrolyzed type I II III V & X Collagen
• Dietary Supplements - 90 capsules
• Support Joints & bones
• Rejuvenate Skin
• Promotes Healthy Hair & Nails
• One right side supplement fact and left side precaution and instruction content. ( Please find the content of the right and left side of the bottle attached)
Nice to have
• Nice to have something that shows elements bring together to create something strong or beautiful. Our brand name is Vellow Naturals. Vellow is an assembly of beams or other elements that creates a rigid structure. This is to show our supplements help to provide the elements to have strong and healthy life

```html
<!DOCTYPE html>
<html lang="en">
<head>
<meta charset="utf-8">
<title>Vellow Naturals – Omni Dermal Capsules Label</title>
<link href="https://fonts.googleapis.com/css2?family=Cinzel:wght@400;600;700&family=Libre+Baskerville:wght@400;700&family=Roboto+Condensed:wght@400;500;700&family=Tinos:wght@400;700&family=Montserrat:wght@600&display=swap" rel="stylesheet">
<style>
  :root {
    --page: #e4e4e4;
    --label-white: #f7f7f7;
    --panel-white: #ffffff;
    --gold: #c9a24a;
    --gold-dark: #a57d2c;
    --red: #9d2a19;
    --red-dark: #7f1f11;
    --ribbon: #4f3a1c;
    --ink: #333333;
    --ink-dark: #3a3a3a;
    --warn-red: #b2301f;
    --white: #ffffff;
    --black: #111111;
  }
  * { box-sizing: border-box; margin: 0; padding: 0; }
  html, body { width: 1082px; height: 1200px; overflow: hidden; }
  body { background: var(--page); position: relative; font-family: "Tinos", serif; color: var(--ink); }

  .label {
    position: absolute; left: 20px; top: 386px;
    width: 1042px; height: 428px;
    background: var(--label-white);
    overflow: hidden;
  }
  .band {
    position: absolute; left: 0; top: 272px; width: 100%; height: 156px;
    background: linear-gradient(180deg, var(--red) 0%, var(--red-dark) 100%);
    border-top: 2px solid var(--gold);
  }
  .front-shape { position: absolute; left: 0; top: 0; width: 1042px; height: 274px; }

  /* Left panel */
  .info-box {
    position: absolute; left: 36px; width: 242px;
    border: 1px solid var(--gold); border-radius: 3px;
    padding: 9px 9px 6px 11px;
    font-size: 8.6px; line-height: 1.28; color: var(--ink);
  }
  .info-box .tab {
    position: absolute; left: 14px; top: -6px;
    background: linear-gradient(90deg, var(--gold-dark), var(--gold));
    color: var(--white); font-size: 7.6px; letter-spacing: .3px;
    padding: 0 10px; line-height: 11px; text-transform: uppercase;
  }
  .suggested { top: 47px; height: 67px; text-align: justify; }
  .caution { top: 124px; height: 65px; }
  .warning {
    top: 200px; height: 64px; text-align: center; color: var(--warn-red);
    font-size: 9.4px; line-height: 1.32; padding-top: 6px; text-transform: uppercase;
  }

  .symbols { position: absolute; left: 136px; top: 283px; display: flex; gap: 12px; }
  .symbols svg { width: 17px; height: 17px; }
  .disclaimer {
    position: absolute; left: 36px; top: 309px; width: 242px; height: 32px;
    border: 1px solid var(--gold); border-radius: 3px;
    color: var(--white); font-size: 7px; line-height: 1.25; text-align: center; padding: 3px 6px 0;
    font-weight: 400;
  }
  .lot { position: absolute; left: 36px; top: 405px; width: 256px; color: var(--gold); font-size: 8px; text-align: center; }

  /* Front panel */
  .brand {
    position: absolute; left: 370px; top: 46px; width: 302px; text-align: center;
    display: flex; align-items: center; justify-content: center; gap: 6px;
    font-family: "Montserrat", sans-serif; font-weight: 600; font-size: 22px; color: var(--ink-dark);
  }
  .brand .dot { width: 10px; height: 10px; border-radius: 50%; background: #7cb342; }
  .product-name {
    position: absolute; left: 370px; top: 96px; width: 302px; text-align: center;
    font-family: "Libre Baskerville", serif; font-weight: 700; font-size: 33px; line-height: 1.02;
    color: var(--ink-dark); letter-spacing: -.5px;
  }
  .product-form {
    position: absolute; left: 370px; top: 194px; width: 302px; text-align: center;
    font-family: "Libre Baskerville", serif; font-weight: 700; font-size: 28px; color: var(--warn-red); letter-spacing: 1px;
  }
  .subtitle {
    position: absolute; left: 370px; top: 238px; width: 302px; text-align: center;
    font-size: 13px; color: var(--ink);
  }
  .ribbon {
    position: absolute; left: 404px; top: 256px; width: 234px; height: 17px;
    background: linear-gradient(90deg, #3e2d14, var(--ribbon), #3e2d14);
    color: var(--white); font-size: 10.6px; text-align: center; line-height: 17px; white-space: nowrap;
  }
  .benefits { position: absolute; left: 404px; top: 300px; width: 240px; display: flex; align-items: flex-start; }
  .benefit { display: flex; gap: 4px; color: var(--white); font-size: 9.6px; line-height: 1.25; padding: 0 5px; }
  .benefit + .benefit { border-left: 1.5px dotted var(--white); }
  .benefit .icon { width: 18px; height: 18px; border-radius: 50%; background: rgba(255,255,255,.35); flex: none; }
  .count {
    position: absolute; left: 404px; top: 358px; width: 234px; text-align: center;
    font-family: "Cinzel", serif; font-weight: 600; font-size: 23px; color: var(--white); letter-spacing: 1px;
  }
  .count small { font-size: 19px; }
  .dietary {
    position: absolute; left: 426px; top: 390px; width: 188px; height: 22px;
    border: 1px solid var(--gold); color: var(--white); text-align: center;
    font-family: "Cinzel", serif; font-size: 12.5px; line-height: 20px; letter-spacing: 1.2px; white-space: nowrap;
  }

  /* Supplement facts */
  .facts {
    position: absolute; left: 760px; top: 42px; width: 248px; height: 222px;
    border: 1.5px solid var(--black); border-radius: 4px; background: var(--white);
    font-family: "Roboto Condensed", sans-serif; color: var(--black); padding: 0 4px;
    display: flex; flex-direction: column; overflow: hidden;
  }
  .facts h2 {
    font-weight: 500; font-size: 28px; text-align: center; line-height: 38px; height: 40px;
    white-space: nowrap; border-bottom: 1px solid var(--black); margin: 0 6px; letter-spacing: -.2px;
  }
  .facts .serving { font-size: 10.5px; font-weight: 500; line-height: 1.4; padding: 4px 6px 4px; }
  .facts .thick { height: 6px; background: var(--black); flex: none; }
  .facts .thick.lower { height: 5px; }
  .facts .head { display: flex; justify-content: flex-end; gap: 18px; font-size: 9px; font-weight: 500; padding: 3px 4px 2px; border-bottom: 1px solid var(--black); margin: 0 2px; }
  .facts .row { display: grid; grid-template-columns: 1fr 70px 22px; font-size: 11px; font-weight: 500; padding: 3px 6px 4px; line-height: 1.35; border-bottom: 1px solid var(--black); margin: 0 2px; }
  .facts .ingredients { font-family: "Tinos", serif; font-size: 7.4px; line-height: 1.22; padding: 4px 6px 4px; color: var(--black); }
  .facts .note { font-size: 9px; font-weight: 500; padding: 3px 6px 0; white-space: nowrap; }

  .allergens { position: absolute; left: 763px; top: 303px; list-style: none; color: var(--white); font-size: 8.8px; line-height: 1.55; }
  .allergens li::before { content: "•"; color: var(--gold); margin-right: 5px; }
  .allergens b { font-weight: 700; }
  .badges { position: absolute; left: 782px; top: 361px; display: flex; gap: 10px; }
  .badges span { width: 35px; height: 35px; border-radius: 50%; background: #2a2a2a; border: 2px solid #d8d8d8; }
</style>
</head>
<body>
<main class="label">
  <div class="band"></div>

  <svg class="front-shape" viewBox="0 0 1042 274" aria-hidden="true">
    <defs>
      <linearGradient id="gold-edge" x1="0" y1="0" x2="0" y2="1">
        <stop offset="0" stop-color="#e9cf7d"/>
        <stop offset=".5" stop-color="#b98a2f"/>
        <stop offset="1" stop-color="#e3c46a"/>
      </linearGradient>
    </defs>
    <path d="M364,0 C414,80 414,200 388,274 L654,274 C628,200 628,80 678,0 Z" fill="url(#gold-edge)"/>
    <path d="M372,0 C422,80 422,200 396,274 L646,274 C620,200 620,80 670,0 Z" fill="var(--panel-white)"/>
  </svg>

  <!-- Left side: use & precautions -->
  <section class="info-box suggested">
    <span class="tab">Suggested Use</span>
    Take three (3) capsules one or more times a day or as directed by your heath care professional. For best results take on an empty stomach with an a 8oz. glass of water.
  </section>
  <section class="info-box caution">
    <span class="tab">Caution</span>
    Do not exceed recommended dose. Pregnant or nursing mothers, children under the age of 18, and individuals with a known medical condition should consult a physician before using this or any dietary supplement.
  </section>
  <section class="info-box warning">
    Keep out of reach of children.<br>Do not use if safety seal is damaged<br>or missing.<br>Store in a cool, dry place.
  </section>

  <div class="symbols">
    <svg viewBox="0 0 20 20" aria-label="Warning"><path d="M10 2 L19 18 H1 Z" fill="none" stroke="#fff" stroke-width="1.6"/><rect x="9.2" y="7" width="1.6" height="6" fill="#fff"/><rect x="9.2" y="14.5" width="1.6" height="1.6" fill="#fff"/></svg>
    <svg viewBox="0 0 20 20" aria-label="Recyclable"><path d="M10 3 L14 9 M14 9 L16 6 M6 8 L3 14 H9 M12 16 H17 L14 10" fill="none" stroke="#fff" stroke-width="2"/></svg>
    <svg viewBox="0 0 20 20" aria-label="Dispose responsibly"><rect x="10" y="8" width="6" height="10" fill="none" stroke="#fff" stroke-width="1.5"/><circle cx="5" cy="4" r="2" fill="#fff"/><path d="M5 7 V13 M5 13 L3 18 M5 13 L7 18 M5 9 L9 7" stroke="#fff" stroke-width="1.5"/></svg>
  </div>
  <p class="disclaimer">These statements have not been evaluated by the Food and Drug Administration. This product is not intended to diagnose, treat, cure or prevent any disease.</p>
  <p class="lot">LOT# and Expiration date printed on bottom of Bottle.</p>

  <!-- Front -->
  <div class="brand"><span class="dot"></span>Vellow Naturals</div>
  <h1 class="product-name">OMNI<br>DERMAL</h1>
  <div class="product-form">CAPSULES</div>
  <div class="subtitle">Hydrolyzed Protein</div>
  <div class="ribbon">Food Source Collagen | Type I, II, III, V &amp; X</div>

  <div class="benefits">
    <div class="benefit"><span class="icon" role="img" aria-label="Joint and bone icon"></span>Support<br>Joints &amp;<br>bones</div>
    <div class="benefit"><span class="icon" role="img" aria-label="Skin care icon"></span>Rejuvenate<br>Skin</div>
    <div class="benefit"><span class="icon" role="img" aria-label="Hair and nails icon"></span>Promotes<br>Healthy<br>Hair &amp; Nails</div>
  </div>
  <div class="count">90 <small>CAPSULES</small></div>
  <div class="dietary">DIETARY SUPPLEMENTS</div>

  <!-- Right side: supplement facts -->
  <section class="facts">
    <h2>Supplement Facts</h2>
    <div class="serving">Serving Size: 3 Capsules<br>Servings Per Container: 30</div>
    <div class="thick"></div>
    <div class="head"><span>Amount Per Serving</span><span>%DV</span></div>
    <div class="row"><span>Premium Collagen<br>Protein Complex</span><span>1500mg</span><span>**</span></div>
    <p class="ingredients">Bovine Collagen Peptides, Hydrolyzed chicken Collagen Peptides. Pure Hydrolyzed Marine Collagen Peptides, Eggshel Membrane Collagen Peptides, Avian Sternum Collagen Peptides.</p>
    <div class="thick lower"></div>
    <p class="note">** Daily Value not established (DV)</p>
  </section>

  <ul class="allergens">
    <li><b>Inactive Ingradients:</b> Gelatin Capsules</li>
    <li><b>Contains:</b> Egg, Fish</li>
    <li><b>Contains no added:</b> Milk, Tree Nuts, Wheat, Peanuts, Soy</li>
  </ul>
  <div class="badges" aria-hidden="true"><span></span><span></span><span></span><span></span><span></span></div>
</main>
</body>
</html>
```